Business card design for new eCommerce site focusing on integrity and strong businsess tactics

We need a business card that will stand out and be memorable. Something with color that matches our company logo colors. Think high end version of Pactivo. There are 2 logos provided. The parent company is called Amber Ledge Partners and we are presenting a new and very exciting eCommerce site called BrightHarborTrade.example.

Target Market(s)

Our target markets are in the Activities, Food and Beverage, Health and Beauty

Industry/Entity Type

Marketing

Contact Information for Business Card

We have 4 members that need cards...I will provide all info to the winner of the design contest
Business Address is
4870 West 63rd Avenue, Suite C207
Phoenix AZ 85731

Font styles to use
Serif
Sans Serif

Colors

Designer to choose colors to be used in the design.

Requirements
Must have
• The card must be memorable...should be unique in design but must exude integrity and be playful .
• I have provided several colors or our parent company...please feel free to use which ever
Nice to have
• I will leave this up to you. Feel free to use other images of your choosing that wraps around our client.....Activities, Dining, Health, Beauty
Should not have
• just dont be boring

```html
<!DOCTYPE html>
<html lang="en">
<head>
<meta charset="utf-8">
<title>Amber Ledge Partners – Business Cards</title>
<link rel="stylesheet" href="https://fonts.googleapis.com/css2?family=Mulish:wght@400;600;700&display=swap">
<style>
  :root {
    --backdrop: #1e1e1e;
    --brand-blue: #1f74ad;
    --brand-blue-light: #2f86bf;
    --brand-green: #6cba3a;
    --ink: #5c5c5c;
    --ink-strong: #2a6ea6;
    --card-white: #ffffff;
  }
  html, body {
    margin: 0;
    padding: 0;
    width: 1200px;
    height: 897px;
    overflow: hidden;
    background: var(--backdrop);
    font-family: "Mulish", sans-serif;
  }
  .canvas {
    position: relative;
    width: 1200px;
    height: 897px;
  }
  .card {
    position: absolute;
    width: 546px;
    height: 308px;
    left: 324px;
    box-sizing: border-box;
    overflow: hidden;
  }
  /* Front */
  .card-front {
    top: 130px;
    background: linear-gradient(135deg, var(--brand-blue) 0%, var(--brand-blue-light) 100%);
    color: var(--card-white);
    text-align: center;
  }
  .front-ring {
    position: absolute;
    left: 50%;
    top: 62px;
    width: 64px;
    height: 64px;
    margin-left: -32px;
    border: 3px solid var(--card-white);
    border-radius: 50%;
    box-sizing: border-box;
  }
  .front-name {
    position: absolute;
    left: 0;
    right: 0;
    top: 178px;
    font-size: 36px;
    font-weight: 700;
    letter-spacing: 0.5px;
  }
  .front-url {
    position: absolute;
    left: 0;
    right: 0;
    top: 272px;
    font-size: 12px;
    letter-spacing: 1.6px;
  }
  /* Back */
  .card-back {
    top: 471px;
    background: var(--card-white);
  }
  .brand-dot {
    position: absolute;
    left: 64px;
    top: 42px;
    width: 22px;
    height: 22px;
    border-radius: 50%;
    background: var(--brand-blue);
  }
  .brand-name {
    position: absolute;
    left: 96px;
    top: 36px;
    font-size: 24px;
    font-weight: 600;
    color: var(--brand-green);
    letter-spacing: -0.3px;
  }
  .brand-tagline {
    position: absolute;
    left: 97px;
    top: 74px;
    font-size: 12px;
    letter-spacing: 1px;
    color: #444;
  }
  .person {
    position: absolute;
    left: 113px;
    top: 128px;
  }
  .person-name {
    font-size: 16px;
    font-weight: 700;
    color: var(--ink-strong);
    letter-spacing: 0.4px;
  }
  .person-role {
    font-size: 14px;
    color: var(--ink);
    margin-top: 1px;
  }
  .contact-list {
    position: absolute;
    left: 113px;
    top: 182px;
    margin: 0;
    padding: 0;
    list-style: none;
    font-size: 12px;
    color: var(--ink);
    letter-spacing: 0.5px;
  }
  .contact-list li {
    display: flex;
    align-items: center;
    height: 17.5px;
  }
  .contact-list svg {
    width: 10px;
    height: 10px;
    margin-right: 12px;
    fill: none;
    stroke: var(--brand-blue);
    stroke-width: 1.6;
  }
  .address {
    position: absolute;
    left: 113px;
    top: 245px;
    font-size: 12px;
    line-height: 17.5px;
    color: var(--ink);
    letter-spacing: 0.5px;
    font-style: normal;
  }
  .accent-bar {
    position: absolute;
    left: 0;
    right: 0;
    bottom: 0;
    height: 6px;
    background: linear-gradient(90deg, var(--brand-green) 0 114px, var(--card-white) 114px 117px, var(--brand-blue) 117px 100%);
  }
</style>
</head>
<body>
<main class="canvas">
  <section class="card card-front" aria-label="Card front">
    <div class="front-ring"></div>
    <div class="front-name">Amber Ledge Partners</div>
    <div class="front-url">www.amberledgepartners.example</div>
  </section>

  <section class="card card-back" aria-label="Card back">
    <div class="brand-dot"></div>
    <div class="brand-name">BrightHarborTrade.example</div>
    <div class="brand-tagline">Activities-Dining-Health-Beauty</div>

    <div class="person">
      <div class="person-name">Daniel Reyes</div>
      <div class="person-role">Founder</div>
    </div>

    <ul class="contact-list">
      <li>
        <svg viewBox="0 0 10 10" aria-hidden="true"><rect x="2.5" y="0.8" width="5" height="8.4" rx="0.8"/></svg>
        0420 555 318
      </li>
      <li>
        <svg viewBox="0 0 10 10" aria-hidden="true"><rect x="0.8" y="2" width="8.4" height="6" fill="#1f74ad" stroke="none"/><path d="M0.8 2 L5 5.5 L9.2 2" stroke="#fff" stroke-width="1"/></svg>
        info@brightharbortrade.example
      </li>
      <li>
        <svg viewBox="0 0 10 10" aria-hidden="true"><circle cx="4.2" cy="4.2" r="3"/><line x1="6.4" y1="6.4" x2="9.2" y2="9.2"/></svg>
        www.brightharbortrade.example
      </li>
    </ul>

    <address class="address">
      4870 West 63rd Avenue, Suite<br>
      C207 Phoenix AZ 85731
    </address>

    <div class="accent-bar"></div>
  </section>
</main>
</body>
</html>
```